Business card for Eyelash extension salon in Beverly Hills,California USA

We need new business card for our salon in Beverly Hills. The salon name is 'Lashvera' . We would like to have...Business name: Lashvera Name of person: will provide later Address 4720 N.Alder Crest Ave Beverly Hills , CA 90210 Phone: will provide later (Text only) Web: www.lashverastudio.example Snapgrid icon, Circlebook icon follow us for seasonal campaign and news @lashverastudiolounge Design should look elegant, high-end, clean, simple, cohesive with my brand. Please refer my brand board. Business name color will be metallic bronzy color. Im thinking grey background or white background. Thanks

Target Market(s)

25-35. Gender neutral. People who are in Entertainment business industry.
This is High-end Eyelash extension salon in Beverly Hills

Industry/Entity Type

Beauty Salon

Contact Information for Business Card

Business name: Lashvera
Name of person: will provide later
Address 4720 N.Alder Crest Ave Beverly Hills , CA 90210
Phone: will provide later (Text only)
Web: www.lashverastudio.example
Snapgrid icon, Circlebook icon
follow us for seasonal campaign and news @lashverastudiolounge

Requirements
Must have
• Beautiful, elegant, clean and simple look but very attractive and modern
Should not have
• We don't like too clutter, too busy designs.

```html
<!DOCTYPE html>
<html lang="en">
<head>
<meta charset="utf-8">
<title>Lashvera Business Card</title>
<link rel="stylesheet" href="https://fonts.googleapis.com/css2?family=Playfair+Display:wght@400;700&family=Merriweather:wght@300&display=swap">
<style>
  :root {
    --canvas: #dcdcdc;
    --card-front: #ffffff;
    --card-back: #a9a9a9;
    --bronze: #8a6548;
    --gold: #e6c45e;
    --muted: #9a9a9a;
    --ink: #4e4e4e;
    --rule: #a8a8a8;
    --white: #ffffff;
  }
  * { margin: 0; padding: 0; box-sizing: border-box; }
  html, body { width: 1200px; height: 960px; overflow: hidden; }
  body { background: var(--canvas); position: relative; font-family: "Merriweather", Georgia, serif; }

  .card { position: absolute; width: 600px; box-shadow: 2px 3px 6px rgba(0,0,0,0.25); }
  .card--front { left: 302px; top: 122px; height: 336px; background: var(--card-front); }
  .card--back { left: 299px; top: 495px; height: 343px; background: var(--card-back); }

  .wordmark { position: absolute; font-family: "Playfair Display", Georgia, serif; font-weight: 400; line-height: 1; }
  .card--front .wordmark { right: 38px; top: 78px; font-size: 56px; color: var(--bronze); }
  .card--back .wordmark { left: 0; right: 0; top: 118px; text-align: center; font-size: 66px; color: var(--gold); }

  .person { position: absolute; left: 33px; top: 198px; right: 38px; }
  .person__name { font-family: "Playfair Display", Georgia, serif; font-weight: 700; font-size: 26px; color: var(--bronze); letter-spacing: 0.5px; line-height: 1; }
  .person__role { display: flex; align-items: center; gap: 4px; margin-top: 4px; }
  .person__title { font-family: "Playfair Display", Georgia, serif; font-size: 15px; color: var(--muted); letter-spacing: 0.5px; line-height: 1; }
  .person__rule { flex: 1; height: 1px; background: var(--rule); }

  .contact { position: absolute; left: 33px; top: 255px; list-style: none; }
  .contact__item { display: flex; align-items: center; gap: 7px; height: 19.5px; font-size: 13.5px; font-weight: 300; color: var(--ink); }
  .contact__icon { width: 14px; height: 14px; fill: var(--ink); flex: none; }

  .address { position: absolute; right: 36px; top: 275px; text-align: right; font-style: normal; font-size: 13.5px; font-weight: 300; color: var(--ink); line-height: 19.5px; }

  .social { position: absolute; left: 0; right: 0; top: 283px; display: flex; justify-content: center; gap: 2px; }
  .social__badge { width: 24px; height: 26px; fill: var(--white); }
</style>
</head>
<body>
  <section class="card card--front" aria-label="Business card front">
    <div class="wordmark">Lashvera</div>

    <div class="person">
      <div class="person__name">MIREI</div>
      <div class="person__role">
        <span class="person__title">OWNER</span>
        <span class="person__rule"></span>
      </div>
    </div>

    <ul class="contact">
      <li class="contact__item">
        <svg class="contact__icon" viewBox="0 0 24 24" aria-hidden="true"><path d="M6.6 10.8c1.4 2.8 3.8 5.1 6.6 6.6l2.2-2.2c.3-.3.7-.4 1-.2 1.1.4 2.3.6 3.6.6.6 0 1 .4 1 1V20c0 .6-.4 1-1 1C10.6 21 3 13.4 3 4c0-.6.4-1 1-1h3.5c.6 0 1 .4 1 1 0 1.3.2 2.5.6 3.6.1.3 0 .7-.2 1z"/></svg>
        310.555.0142
      </li>
      <li class="contact__item">
        <svg class="contact__icon" viewBox="0 0 24 24" aria-hidden="true"><path d="M3 5h18v14H3z M3 5l9 7 9-7" fill="none" stroke="#4e4e4e" stroke-width="0"/><path d="M3 6v12h18V6l-9 7z M3.5 5h17L12 11.5z"/></svg>
        hello@lashverastudio.example
      </li>
      <li class="contact__item">
        <svg class="contact__icon" viewBox="0 0 24 24" aria-hidden="true"><circle cx="12" cy="12" r="10"/><path d="M7 8c2 0 3 1 3 3s2 2 2 4-1 3-1 4M14 4c0 2 2 3 4 3s2 2 3 3" fill="none" stroke="#ffffff" stroke-width="1.6"/></svg>
        www.lashverastudio.example
      </li>
    </ul>

    <address class="address">
      4720 N.Alder Crest Ave<br>
      Beverly Hills, CA 90210
    </address>
  </section>

  <section class="card card--back" aria-label="Business card back">
    <div class="wordmark">Lashvera</div>
    <div class="social" aria-label="Social profiles">
      <svg class="social__badge" viewBox="0 0 24 26" role="img" aria-label="Circlebook profile"><polygon points="12,0 24,6.5 24,19.5 12,26 0,19.5 0,6.5"/></svg>
      <svg class="social__badge" viewBox="0 0 24 26" role="img" aria-label="Snapgrid profile"><polygon points="12,0 24,6.5 24,19.5 12,26 0,19.5 0,6.5"/></svg>
      <svg class="social__badge" viewBox="0 0 24 26" role="img" aria-label="Review listing"><polygon points="12,0 24,6.5 24,19.5 12,26 0,19.5 0,6.5"/></svg>
    </div>
  </section>
</body>
</html>
```